2021 Summer Ads Hollis Bay Custom Homes

We need a re-design of our summer ad run for our customer, Hollis Bay Custom Homes. They are custom home builders in the mostly rural parts of West Virginia, USA. They are known for their "Forever Home" tagline. We'd like two designed ads with the main difference being just the custom home that's featured. These designs should be for a Zintrola banner like 300 x 250 and square ad like 250 x 250. For inspiration please visit the Hollis Bay Custom Homes website at www dot hollisbaycustomhomes dot com

Target Market(s)

consumers / new home shoppers

Industry/Entity Type

Consumer

Requirements
Must have
• HBCH logo
Price Lock Available!
Custom home pic
Learn more >
small CFRM logo mark

```html
<!DOCTYPE html>
<html lang="en">
<head>
<meta charset="utf-8">
<title>Hollis Bay Custom Homes – Summer Ad Set</title>
<link rel="stylesheet" href="https://fonts.googleapis.com/css2?family=Montserrat:wght@300;400;600;700;800;900&family=Poppins:wght@600&display=swap">
<style>
  :root{
    --canvas:#e4e4e4;
    --ink:#1e2130;
    --ink-deep:#15171f;
    --red:#e31b2d;
    --red-deep:#9e1020;
    --white:#ffffff;
    --navy:#1c2f8f;
  }
  *{box-sizing:border-box;margin:0;padding:0}
  html,body{width:1168px;height:1200px;overflow:hidden;background:var(--canvas)}
  body{position:relative;font-family:"Montserrat",sans-serif;color:var(--white)}

  .ad{position:absolute;overflow:hidden;background:var(--ink)}
  .ad--banner{width:267px;height:223px}
  .ad--square{width:178px;height:178px}
  .ad > *{position:absolute}
  .photo{inset:0}
  .shapes{inset:0;width:100%;height:100%}

  .photo--barn{background:linear-gradient(165deg,#4f7a3e 0%,#7fa06a 22%,#b9bcb6 38%,#b8382b 52%,#8e2720 70%,#a69a8a 88%,#c9bfae 100%)}
  .photo--farmhouse{background:linear-gradient(160deg,#3d6a35 0%,#6f8f5a 18%,#d8dcd6 40%,#eef0ec 55%,#2c2f36 72%,#5b5f58 84%,#3f7a2c 100%)}
  .photo--estate{background:linear-gradient(180deg,#4e7a3f 0%,#c8cbc6 40%,#b4392d 60%,#d9d6cf 80%,#a8a090 100%)}
  .photo--white-modern{background:linear-gradient(170deg,#d9dde3 0%,#f3f4f4 40%,#c9ccd0 62%,#5f8a3d 84%,#3f6d2a 100%)}
  .photo--lakehouse{background:linear-gradient(165deg,#8a93b8 0%,#c7a7b8 18%,#2b5fa8 34%,#e9e2d4 50%,#c98a4a 66%,#7a5238 82%,#4a3626 100%)}
  .photo--colonial{background:linear-gradient(165deg,#d7dbe0 0%,#9aa3ad 30%,#7c8692 52%,#c9cdd2 70%,#6d737b 100%)}

  .brand{font-weight:700;letter-spacing:.14em;text-transform:uppercase;white-space:nowrap;color:var(--white)}

  .headline{font-weight:800;text-transform:uppercase;white-space:nowrap;color:var(--white)}
  .headline span{display:block}
  .headline .light{font-weight:300}
  .headline .accent{color:var(--red)}
  .headline--heavy{font-weight:900;letter-spacing:-.01em}

  .price-lock{font-weight:700;text-transform:uppercase;white-space:nowrap;color:var(--white)}

  .cta{display:flex;align-items:center;justify-content:center;gap:4px;font-weight:700;text-transform:uppercase;white-space:nowrap;color:var(--white)}
  .cta--outline{border:1px solid var(--white);border-radius:2px}
  .cta--red{background:var(--red);border-radius:3px}
  .cta--pill{background:var(--red);border-radius:20px}
  .cta--dark{background:var(--ink);border-radius:3px}
  .cta__arrow{display:inline-flex;align-items:center;justify-content:center;border-radius:50%;background:var(--red);color:var(--white);font-weight:800;line-height:1}
  .cta__arrow--ring{background:none;border:1px solid var(--white)}
  .cta__arrow--block{border-radius:0 3px 3px 0;height:100%;background:var(--red-deep)}

  .seal{line-height:1;color:var(--white);text-align:left}
  .seal__name{display:block;font-weight:800;letter-spacing:-.02em}
  .seal__sub{display:block;font-weight:400;font-size:3.4px;line-height:1.2;margin-top:1px}
</style>
</head>
<body>

<!-- Row 1 -->
<article class="ad ad--banner" style="left:60px;top:47px">
  <div class="photo photo--barn" role="img" aria-label="Photo of a red board-and-batten barn home with grey roof and trees"></div>
  <svg class="shapes" viewBox="0 0 267 223" preserveAspectRatio="none" aria-hidden="true">
    <polygon points="0,0 165,0 110,130 140,223 0,223" fill="var(--ink)"/>
    <polygon points="165,0 202,0 142,126 160,223 140,223 110,130" fill="var(--red)"/>
    <circle cx="144" cy="170" r="10" fill="var(--ink)"/>
    <circle cx="170" cy="170" r="10" fill="var(--red-deep)"/>
    <circle cx="194" cy="170" r="10" fill="var(--red)"/>
  </svg>
  <div class="brand" style="left:8px;top:38px;font-size:10px">Hollis Bay</div>
  <div class="headline" style="left:10px;top:71px;font-size:12.5px;line-height:15px">
    <span class="light">Start Building</span><span>Your Forever</span><span>Home Today!</span>
  </div>
  <div class="price-lock" style="left:10px;top:123px;font-size:6.8px">Price Lock Available!</div>
  <div class="cta cta--outline" style="left:9px;top:143px;width:70px;height:19px;font-size:5.2px">Learn More <span class="cta__arrow" style="width:9px;height:9px;font-size:7px">›</span></div>
  <div class="seal" style="left:12px;top:177px"><span class="seal__name" style="font-size:12px">CFRM</span><span class="seal__sub">Certified Residential<br>Frame Members</span></div>
</article>

<article class="ad ad--square" style="left:360px;top:47px">
  <div class="photo photo--barn" role="img" aria-label="Photo of a red barn-style home with white trim and cupola"></div>
  <svg class="shapes" viewBox="0 0 178 178" preserveAspectRatio="none" aria-hidden="true">
    <polygon points="0,0 68,0 108,100 150,178 0,178" fill="var(--ink)"/>
    <polygon points="68,0 82,0 125,95 178,150 178,178 150,178 108,100" fill="var(--red)"/>
  </svg>
  <div class="brand" style="left:9px;top:18px;font-size:8px">Hollis Bay</div>
  <div class="headline" style="left:8px;top:62px;font-size:10.5px;line-height:13.5px">
    <span class="light">Start</span><span class="light">Building</span><span>Your Forever</span><span>Home Today!</span>
  </div>
  <div class="price-lock" style="left:8px;top:125px;font-size:6px">Price Lock Available!</div>
  <div class="cta cta--outline" style="left:9px;top:141px;width:63px;height:20px;font-size:5.2px">Learn More</div>
  <div class="seal" style="left:104px;top:155px"><span class="seal__name" style="font-size:10px">CFRM</span><span class="seal__sub">Certified Residential</span></div>
</article>

<article class="ad ad--banner" style="left:629px;top:47px">
  <div class="photo photo--farmhouse" role="img" aria-label="Photo of a white farmhouse with black garage doors and stone base"></div>
  <svg class="shapes" viewBox="0 0 267 223" preserveAspectRatio="none" aria-hidden="true">
    <polygon points="0,0 150,0 95,130 175,223 0,223" fill="var(--ink)"/>
    <polygon points="150,0 182,0 125,120 205,223 175,223 95,130" fill="var(--red)"/>
    <polygon points="182,0 192,0 135,118 182,200 125,120" fill="var(--red-deep)"/>
  </svg>
  <div class="brand" style="left:12px;top:56px;font-size:10.5px">Hollis Bay</div>
  <div class="headline headline--heavy" style="left:12px;top:80px;font-size:16px;line-height:18.5px">
    <span>Start</span><span>Building</span><span>Your Forever</span><span>Home Today</span>
  </div>
  <div class="price-lock" style="left:12px;top:160px;font-size:7px">Price Lock Available!</div>
  <div class="cta cta--outline" style="left:13px;top:184px;width:70px;height:19px;font-size:5.2px">Learn More <span class="cta__arrow" style="width:9px;height:9px;font-size:7px">›</span></div>
  <div class="seal" style="left:97px;top:185px"><span class="seal__name" style="font-size:12px">CFRM</span><span class="seal__sub">Certified Residential<br>Frame Members</span></div>
</article>

<article class="ad ad--square" style="left:926px;top:47px">
  <div class="photo photo--farmhouse" role="img" aria-label="Photo of a white farmhouse with cupola and dark garage doors"></div>
  <svg class="shapes" viewBox="0 0 178 178" preserveAspectRatio="none" aria-hidden="true">
    <polygon points="0,35 95,118 178,45 178,62 95,128 0,55" fill="var(--red)"/>
    <polygon points="0,55 95,128 178,62 178,178 0,178" fill="var(--ink)"/>
  </svg>
  <div class="brand" style="left:10px;top:102px;font-size:7.5px">Hollis Bay</div>
  <div class="headline headline--heavy" style="left:9px;top:121px;font-size:11.5px;line-height:12.5px">
    <span>Start Building</span><span>Your Forever</span><span>Home Today</span>
  </div>
  <div class="price-lock" style="left:9px;top:163px;font-size:5.8px">Price Lock Available!</div>
  <div class="seal" style="left:135px;top:131px"><span class="seal__name" style="font-size:10px">CFRM</span><span class="seal__sub">Certified Residential</span></div>
  <div class="cta cta--red" style="left:121px;top:158px;width:50px;height:13px;font-size:4.6px">Learn More</div>
</article>

<!-- Row 2 -->
<article class="ad ad--banner" style="left:60px;top:326px">
  <div class="photo photo--farmhouse" role="img" aria-label="Photo of a white farmhouse gable with garage doors and flower beds"></div>
  <svg class="shapes" viewBox="0 0 267 223" preserveAspectRatio="none" aria-hidden="true">
    <circle cx="-10" cy="55" r="168" fill="var(--red)"/>
    <circle cx="-18" cy="52" r="158" fill="var(--ink)"/>
  </svg>
  <div class="brand" style="left:14px;top:28px;font-size:10px">Hollis Bay</div>
  <div class="headline" style="left:14px;top:51px;font-size:12px;line-height:13px">
    <span class="light">Start Building</span><span>Your Forever</span><span>Home Today!</span>
  </div>
  <div class="price-lock" style="left:14px;top:95px;font-size:6.8px">Price Lock Available!</div>
  <div class="cta cta--pill" style="left:12px;top:112px;width:67px;height:16px;font-size:5.2px">Learn More <span class="cta__arrow cta__arrow--ring" style="width:10px;height:10px;font-size:7px">›</span></div>
  <div class="seal" style="left:17px;top:138px"><span class="seal__name" style="font-size:12px">CFRM</span><span class="seal__sub">Certified Residential<br>Frame Members</span></div>
</article>

<article class="ad ad--square" style="left:360px;top:326px">
  <div class="photo photo--farmhouse" role="img" aria-label="Photo of a white farmhouse with black garage doors"></div>
  <svg class="shapes" viewBox="0 0 178 178" preserveAspectRatio="none" aria-hidden="true">
    <circle cx="-18" cy="55" r="128" fill="var(--red)"/>
    <circle cx="-24" cy="52" r="120" fill="var(--ink)"/>
  </svg>
  <div class="brand" style="left:10px;top:44px;font-size:7.5px">Hollis Bay</div>
  <div class="headline" style="left:8px;top:60px;font-size:9.5px;line-height:10.5px">
    <span class="light">Start Building</span><span>Your Forever</span><span>Home Today!</span>
  </div>
  <div class="price-lock" style="left:8px;top:98px;font-size:5.5px">Price Lock Available!</div>
  <div class="cta cta--pill" style="left:7px;top:110px;width:60px;height:14px;font-size:4.8px">Learn More</div>
  <div class="seal" style="left:10px;top:131px"><span class="seal__name" style="font-size:10px">CFRM</span><span class="seal__sub">Certified Residential</span></div>
</article>

<article class="ad ad--banner" style="left:629px;top:326px">
  <div class="photo photo--farmhouse" role="img" aria-label="Photo of a white farmhouse with stone base and garden"></div>
  <svg class="shapes" viewBox="0 0 267 223" preserveAspectRatio="none" aria-hidden="true">
    <polygon points="0,0 190,0 70,223 0,223" fill="var(--white)"/>
    <polygon points="190,0 199,0 80,223 70,223" fill="var(--red)"/>
    <polygon points="0,0 18,0 0,32" fill="var(--red)"/>
  </svg>
  <div class="headline" style="left:19px;top:17px;font-family:'Poppins',sans-serif;font-weight:600;text-transform:none;font-size:16.5px;line-height:19px;color:var(--ink)">
    <span class="accent">Start</span><span class="accent">Building</span><span>Your Forever</span><span>Home Today!</span>
  </div>
  <div class="price-lock" style="left:19px;top:97px;font-size:7px;color:var(--red)">Price Lock Available!</div>
  <div class="cta cta--red" style="left:19px;top:114px;width:72px;height:19px;font-size:5.4px;justify-content:space-between;padding-left:9px">Learn More <span class="cta__arrow cta__arrow--block" style="width:13px;font-size:9px">›</span></div>
  <div class="brand" style="left:14px;top:153px;font-size:10px;color:var(--red-deep)">Hollis Bay</div>
  <div class="seal" style="left:14px;top:180px;color:var(--navy)"><span class="seal__name" style="font-size:13px">CFRM</span><span class="seal__sub">Certified Residential<br>Frame Members</span></div>
</article>

<article class="ad ad--square" style="left:926px;top:326px">
  <div class="photo photo--estate" role="img" aria-label="Photo of a red barn-style estate home with white wings"></div>
  <svg class="shapes" viewBox="0 0 178 178" preserveAspectRatio="none" aria-hidden="true">
    <path d="M0,82 Q95,62 178,92 L178,104 Q95,74 0,92 Z" fill="var(--red)"/>
    <path d="M0,92 Q95,74 178,104 L178,178 L0,178 Z" fill="var(--ink)"/>
  </svg>
  <div class="brand" style="left:10px;top:105px;font-size:7.5px">Hollis Bay</div>
  <div class="headline" style="left:9px;top:121px;font-size:10.5px;line-height:11.5px">
    <span class="accent">Start Building</span><span>Your Forever</span><span>Home Today!</span>
  </div>
  <div class="price-lock" style="left:9px;top:160px;font-size:5.6px">Price Lock Available!</div>
  <div class="seal" style="left:130px;top:131px"><span class="seal__name" style="font-size:10px">CFRM</span><span class="seal__sub">Certified Residential</span></div>
  <div class="cta cta--pill" style="left:118px;top:157px;width:56px;height:14px;font-size:4.8px">Learn More</div>
</article>

<!-- Row 3 -->
<article class="ad ad--banner" style="left:60px;top:611px">
  <div class="photo photo--white-modern" role="img" aria-label="Photo of a white modern farmhouse with metal roof and lawn"></div>
  <svg class="shapes" viewBox="0 0 267 223" preserveAspectRatio="none" aria-hidden="true">
    <defs><linearGradient id="panelRed" x1="0" y1="0" x2="1" y2="1"><stop offset="0" stop-color="var(--red-deep)"/><stop offset="1" stop-color="var(--red)"/></linearGradient></defs>
    <circle cx="-28" cy="100" r="188" fill="var(--red)"/>
    <circle cx="-32" cy="100" r="182" fill="var(--white)"/>
    <circle cx="-36" cy="100" r="178" fill="url(#panelRed)"/>
  </svg>
  <div class="brand" style="left:12px;top:33px;font-size:10.5px">Hollis Bay</div>
  <div class="headline" style="left:11px;top:63px;font-size:14px;line-height:17px">
    <span class="light">Start Building</span><span>Your Forever</span><span>Home Today!</span>
  </div>
  <div class="price-lock" style="left:12px;top:121px;font-size:7.4px">Price Lock Available!</div>
  <div class="cta cta--dark" style="left:12px;top:138px;width:72px;height:19px;font-size:5.4px;justify-content:space-between;padding-left:9px">Learn More <span class="cta__arrow cta__arrow--block" style="width:14px;font-size:9px;background:var(--red)">›</span></div>
  <div class="seal" style="left:12px;top:170px"><span class="seal__name" style="font-size:13px">CFRM</span><span class="seal__sub">Certified Residential<br>Frame Members</span></div>
</article>

<article class="ad ad--square" style="left:360px;top:611px">
  <div class="photo photo--white-modern" role="img" aria-label="Photo of a white two-storey farmhouse with porch and trees"></div>
  <svg class="shapes" viewBox="0 0 178 178" preserveAspectRatio="none" aria-hidden="true">
    <path d="M0,84 Q90,70 178,62 L178,76 Q90,82 0,96 Z" fill="var(--red)"/>
    <path d="M0,96 Q90,82 178,76 L178,178 L0,178 Z" fill="var(--ink)"/>
  </svg>
  <div class="brand" style="left:10px;top:105px;font-size:7.5px">Hollis Bay</div>
  <div class="headline headline--heavy" style="left:9px;top:122px;font-size:12.5px;line-height:13px">
    <span class="accent">Start Building</span><span>Your Forever</span><span>Home Today</span>
  </div>
  <div class="price-lock" style="left:9px;top:163px;font-size:5.8px">Price Lock Available!</div>
  <div class="seal" style="left:132px;top:133px"><span class="seal__name" style="font-size:10px">CFRM</span><span class="seal__sub">Certified Residential</span></div>
  <div class="cta cta--red" style="left:116px;top:157px;width:54px;height:14px;font-size:4.6px">Learn More</div>
</article>

<article class="ad ad--banner" style="left:629px;top:611px">
  <div class="photo photo--lakehouse" role="img" aria-label="Photo of a lake house with blue roof, lit screened porches and stone columns at dusk"></div>
  <svg class="shapes" viewBox="0 0 267 223" preserveAspectRatio="none" aria-hidden="true">
    <polygon points="0,0 195,0 95,223 0,223" fill="var(--ink)"/>
    <polygon points="180,0 203,0 104,223 86,223" fill="var(--red)"/>
    <polygon points="0,0 45,0 0,60" fill="var(--red-deep)"/>
  </svg>
  <div class="brand" style="left:18px;top:30px;font-size:10.5px">Hollis Bay</div>
  <div class="headline" style="left:17px;top:63px;font-size:14px;line-height:17px">
    <span class="light">Start Building</span><span>Your Forever</span><span>Home Today!</span>
  </div>
  <div class="price-lock" style="left:18px;top:121px;font-size:7.4px">Price Lock Available!</div>
  <div class="cta cta--red" style="left:18px;top:138px;width:72px;height:19px;font-size:5.4px;justify-content:space-between;padding-left:9px">Learn More <span class="cta__arrow cta__arrow--block" style="width:14px;font-size:9px">›</span></div>
  <div class="seal" style="left:17px;top:174px"><span class="seal__name" style="font-size:13px">CFRM</span><span class="seal__sub">Certified Residential<br>Frame Members</span></div>
</article>

<article class="ad ad--square" style="left:926px;top:611px">
  <div class="photo photo--lakehouse" role="img" aria-label="Photo of a lake house with blue roof and lit porches"></div>
  <svg class="shapes" viewBox="0 0 178 178" preserveAspectRatio="none" aria-hidden="true">
    <polygon points="0,0 125,0 85,178 0,178" fill="var(--ink)"/>
    <polygon points="118,0 132,0 92,178 78,178" fill="var(--red)"/>
    <polygon points="85,172 178,172 178,178 85,178" fill="var(--red)"/>
  </svg>
  <div class="brand" style="left:7px;top:15px;font-size:7.5px">Hollis Bay</div>
  <div class="headline" style="left:5px;top:45px;font-size:10.5px;line-height:13px">
    <span class="light">Start Building</span><span>Your Forever</span><span>Home Today!</span>
  </div>
  <div class="price-lock" style="left:6px;top:88px;font-size:5.6px">Price Lock Available!</div>
  <div class="cta cta--red" style="left:6px;top:103px;width:59px;height:15px;font-size:4.6px;justify-content:space-between;padding-left:7px">Learn More <span class="cta__arrow cta__arrow--block" style="width:11px;font-size:8px">›</span></div>
  <div class="seal" style="left:7px;top:138px"><span class="seal__name" style="font-size:10px">CFRM</span><span class="seal__sub">Certified Residential</span></div>
</article>

<!-- Row 4 -->
<article class="ad ad--banner" style="left:60px;top:908px">
  <div class="photo photo--colonial" role="img" aria-label="Photo of a grey two-storey home with white deck railing"></div>
  <svg class="shapes" viewBox="0 0 267 223" preserveAspectRatio="none" aria-hidden="true">
    <polygon points="0,0 103,0 165,223 0,223" fill="var(--ink)"/>
    <polygon points="103,0 112,0 175,223 165,223" fill="var(--red-deep)"/>
    <polygon points="0,0 50,0 0,34" fill="var(--red)"/>
    <polygon points="150,205 267,180 267,223 150,223" fill="var(--red)"/>
  </svg>
  <div class="brand" style="left:13px;top:62px;font-size:11px">Hollis Bay</div>
  <div class="headline" style="left:12px;top:97px;font-size:15px;line-height:16px">
    <span class="light">Start</span><span class="light">Building</span><span>Your Forever</span><span>Home Today!</span>
  </div>
  <div class="price-lock" style="left:15px;top:166px;font-size:7.4px">Price Lock Available!</div>
  <div class="cta cta--red" style="left:14px;top:183px;width:75px;height:20px;font-size:5.6px">Learn More <span style="font-size:9px">›</span></div>
  <div class="seal" style="left:226px;top:199px"><span class="seal__name" style="font-size:12px">CFRM</span><span class="seal__sub">Certified Residential</span></div>
</article>

<article class="ad ad--square" style="left:360px;top:908px">
  <div class="photo photo--lakehouse" role="img" aria-label="Photo of a blue-roofed lake house with lit porches at dusk"></div>
  <svg class="shapes" viewBox="0 0 178 178" preserveAspectRatio="none" aria-hidden="true">
    <path d="M0,88 Q90,104 178,78 L178,90 Q90,114 0,98 Z" fill="var(--red)"/>
    <path d="M0,98 Q90,114 178,90 L178,178 L0,178 Z" fill="var(--ink)"/>
  </svg>
  <div class="brand" style="left:9px;top:110px;font-size:7.5px">Hollis Bay</div>
  <div class="headline" style="left:8px;top:127px;font-size:10.5px;line-height:11px">
    <span class="accent">Start Building</span><span>Your Forever</span><span>Home Today!</span>
  </div>
  <div class="price-lock" style="left:9px;top:163px;font-size:5.8px">Price Lock Available!</div>
  <div class="seal" style="left:130px;top:133px"><span class="seal__name" style="font-size:10px">CFRM</span><span class="seal__sub">Certified Residential</span></div>
  <div class="cta cta--pill" style="left:117px;top:156px;width:58px;height:14px;font-size:4.8px">Learn More</div>
</article>

</body>
</html>
```